Bramwell Lodge Business Cards design with a logo

I want two Business cards designed with a very modern contemporary logo UNING 1920'S FONT STYLES with the following details

Address:
Bramwell Lodge
17 Pellham Road
Lochbrae
G83 2RN

Details for card 1

Name: Dermot Ashby
email: Dermot.ashby@bramwell.lodge
Tel : +971 52 318 6094
Tel +44 7700 900 318

Details Card 2

Name: Dermot Ashby
email: Neville.osgood@bramwell.lodge
Tel : +971 52 430 9187

Bramwell lodge is a house that was built around 1880 and was used extensively in the 1920's for entertaining and parties in the arts scene, the house again will be resurrected to a modern entertainment venue

If you have any questions feel free to ask

Target Market(s)

The market for this is the young modern crowd

Industry/Entity Type

Entertainment Industry

Contact Information for Business Card

Address:
Bramwell Lodge
17 Pellham Road
Lochbrae
G83 2RN

Details for card 1

Name: Dermot Ashby
Tel : +971 52 318 6094
Tel +44 7700 900 318

Details Card 2

Name: Neville Osgood
Tel : +971 52 430 9187

Logo Text

Bramwell Lodge

Font styles to use
Other font styles liked:
• 1920'S FONT STULES

Requirements
Must have
• Modern Contemporary, whilst taking into consideration the age of the house as detailed above. YOU MUT BE USING 1920'S FONT STYLES
Nice to have
• 1920'S FONT STYLES see attached image if a suggestion
Should not have
• Should not look old or dated

```html
<!DOCTYPE html>
<html lang="en">
<head>
<meta charset="utf-8">
<title>Bramwell Lodge Business Cards</title>
<link rel="stylesheet" href="https://fonts.googleapis.com/css2?family=Federo&display=swap">
<style>
  :root {
    --backdrop: #1b1b1c;
    --card-face: #232324;
    --card-back: #202021;
    --pattern-light: #2e2e30;
    --pattern-dark: #1f1f20;
    --silver: #dcdcdc;
    --muted: #8a8a8a;
    --icon: #9a9a9a;
    --gloss: #111112;
    --gloss-edge: #2c2c2d;
    --rule: #3a3a3b;
  }
  * { margin: 0; padding: 0; box-sizing: border-box; }
  html, body {
    width: 1200px;
    height: 900px;
    overflow: hidden;
    background: var(--backdrop);
  }
  body {
    font-family: "Federo", sans-serif;
    text-transform: uppercase;
    display: flex;
    flex-direction: column;
    align-items: center;
    justify-content: center;
    gap: 44px;
  }
  .card {
    position: relative;
    width: 640px;
    height: 366px;
    border-radius: 3px;
    overflow: hidden;
    box-shadow: 0 10px 24px rgba(0,0,0,0.45);
  }

  /* Front */
  .card--front { background: var(--card-face); }
  .card__pattern {
    position: absolute;
    inset: 0;
    background: radial-gradient(ellipse at 60% 45%, var(--pattern-light), var(--pattern-dark) 80%);
  }
  .brand-name {
    position: absolute;
    left: 0; right: 0;
    top: 128px;
    text-align: center;
    font-size: 58px;
    font-weight: 400;
    letter-spacing: 3px;
    color: var(--silver);
  }
  .front-url {
    position: absolute;
    left: 0; right: 0;
    bottom: 26px;
    text-align: center;
    font-size: 13px;
    letter-spacing: 1.5px;
    color: var(--muted);
  }

  /* Back */
  .card--back {
    background: linear-gradient(160deg, #262627 0%, var(--card-back) 60%, #1b1b1c 100%);
  }
  .holder {
    position: absolute;
    left: 30px;
    top: 118px;
    width: 250px;
    text-align: right;
  }
  .holder__name {
    font-size: 26px;
    letter-spacing: 1px;
    color: var(--gloss);
    text-shadow: 0 1px 0 var(--gloss-edge);
  }
  .holder__role {
    font-size: 12px;
    letter-spacing: 1.5px;
    color: var(--gloss);
    text-shadow: 0 1px 0 var(--gloss-edge);
    margin-top: 2px;
  }
  .divider {
    position: absolute;
    left: 300px;
    top: 100px;
    width: 1px;
    height: 84px;
    background: var(--rule);
  }
  .contacts {
    position: absolute;
    left: 318px;
    top: 100px;
    list-style: none;
  }
  .contacts li {
    display: flex;
    align-items: center;
    gap: 9px;
    font-size: 14px;
    line-height: 21px;
    letter-spacing: 0.5px;
    color: var(--silver);
  }
  .contacts svg { width: 11px; height: 11px; flex: none; }
  .address {
    position: absolute;
    left: 44px;
    bottom: 60px;
    display: flex;
    align-items: center;
    gap: 12px;
    font-size: 15px;
    letter-spacing: 1px;
    color: var(--gloss);
    text-shadow: 0 1px 0 var(--gloss-edge);
  }
  .address__mark {
    width: 16px;
    height: 16px;
    background: var(--gloss);
    box-shadow: 0 1px 0 var(--gloss-edge);
  }
</style>
</head>
<body>

  <section class="card card--front">
    <div class="card__pattern" role="img" aria-label="Art deco diamond and fan pattern in tonal greys covering the card"></div>
    <h1 class="brand-name">Bramwell Lodge</h1>
    <p class="front-url">www.bramwelllodge.com</p>
  </section>

  <section class="card card--back">
    <div class="holder">
      <p class="holder__name">Dermot Ashby</p>
      <p class="holder__role">Director</p>
    </div>
    <div class="divider"></div>
    <ul class="contacts">
      <li>
        <svg viewBox="0 0 12 12" fill="var(--icon)"><path d="M2.5 1h2l1 2.6-1.2.9a6 6 0 0 0 3.2 3.2l.9-1.2 2.6 1v2A1.5 1.5 0 0 1 9.5 11 8.5 8.5 0 0 1 1 2.5 1.5 1.5 0 0 1 2.5 1z"/></svg>
        +971 52 318 6094
      </li>
      <li>
        <svg viewBox="0 0 12 12" fill="var(--icon)"><path d="M1 4c0-1.5 2.5-2.5 5-2.5S11 2.5 11 4v1H8.5V3.8h-5V5H1z"/><rect x="2.5" y="6" width="7" height="4.5" rx="1"/></svg>
        +44 7700 900 318
      </li>
      <li>
        <svg viewBox="0 0 12 12" fill="none" stroke="var(--icon)" stroke-width="1.2"><rect x="1" y="2.5" width="10" height="7"/><path d="M1 2.5l5 4 5-4"/></svg>
        Dermot.ashby@bramwell.lodge
      </li>
      <li>
        <svg viewBox="0 0 12 12" fill="none" stroke="var(--icon)" stroke-width="1"><circle cx="6" cy="6" r="5"/><ellipse cx="6" cy="6" rx="2.2" ry="5"/><path d="M1 6h10"/></svg>
        www.bramwelllodge.com
      </li>
    </ul>
    <p class="address">
      <span class="address__mark"></span>
      Bramwell Lodge, 17 Pellham Road Lochbrae&nbsp; G83 2RN
    </p>
  </section>

</body>
</html>
```